ambitious event and festival agency from austria needs fresh business card design

A new design is due for the new headquarters and the new challenges. We organize events for different target groups from 16 to 60 years. The design should therefore be straightforward and not confused, so we are open to new colors and the logo may also be changed. In general, however, the most interesting suggestions are the most interesting ones. after this order we are looking for more graphics for brightloom facebook instagramm homepage etc A new design is due for the new headquarters and the new challenges. We organize events for different target groups from 16 to 60 years. The design should therefore be straightforward and not confused, so we are open to new colors and the logo may also be changed. In general, however, the most interesting suggestions are the most interesting ones. after this order we are looking for more graphics for brightloom facebook instagramm homepage etc A new design is due for the new headquarters and the new challenges. We organize events for different target groups from 16 to 60 years. The design should therefore be straightforward and not confused, so we are open to new colors and the logo may also be changed. In general, however, the most interesting suggestions are the most interesting ones. after this order we are looking for more graphics for brightloom facebook instagramm homepage etc
Updates

Reason: I am sorry for this decision but i need some more time. No new designs please, there are so many good ones and I will have made a decision in the next 3 days.

Target Market(s)

Industry/Entity Type

Business

Font styles to use
Serif
Sans Serif

Colors

Designer to choose colors to be used in the design.

Requirements
Must have
Nice to have
Should not have

```html
<!DOCTYPE html>
<html lang="de">
<head>
<meta charset="utf-8">
<title>brightloom – Visitenkarte</title>
<link href="https://fonts.googleapis.com/css2?family=Roboto:wght@400;500;700&family=Roboto+Condensed:wght@400;500;700&display=swap" rel="stylesheet">
<style>
  :root {
    --brand-red: #b0243a;
    --brand-grey: #5f6466;
    --ink: #4a4d4f;
    --paper: #f7f7f6;
    --backdrop: #e4e4e4;
    --rule: #b9b9b9;
  }
  * { margin: 0; padding: 0; box-sizing: border-box; }
  html, body {
    width: 1200px; height: 960px; overflow: hidden;
    background: var(--backdrop);
    font-family: "Roboto", Arial, sans-serif;
  }
  .canvas { position: relative; width: 1200px; height: 960px; }

  .card { position: absolute; width: 601px; height: 343px; }
  .card--front { left: 314px; top: 113px; background: var(--paper); }
  .card--back { left: 311px; top: 472px; background: var(--brand-red); }

  .wordmark {
    position: absolute;
    font-family: "Roboto", Arial, sans-serif;
    font-weight: 500;
    letter-spacing: -1px;
    line-height: 1;
    white-space: nowrap;
  }
  .card--front .wordmark {
    left: 50px; top: 143px;
    font-size: 42px; color: var(--brand-grey);
  }
  .card--back .wordmark {
    left: 0; width: 100%; text-align: center; top: 146px;
    font-size: 62px; color: #fff;
  }

  .divider {
    position: absolute; left: 316px; top: 72px;
    width: 1px; height: 170px;
    background: linear-gradient(to bottom, transparent, var(--rule) 20%, var(--rule) 80%, transparent);
  }

  .contact { position: absolute; left: 346px; top: 78px; color: var(--ink); }
  .contact__name {
    font-family: "Roboto Condensed", Arial, sans-serif;
    font-weight: 700; font-size: 21px; color: var(--brand-red);
    letter-spacing: 0.2px; line-height: 24px;
  }
  .contact__role {
    font-family: "Roboto Condensed", Arial, sans-serif;
    font-size: 16px; color: var(--brand-grey); line-height: 20px;
    letter-spacing: 0.3px;
  }
  .contact__address { margin-top: 10px; font-size: 14.5px; line-height: 18.5px; }
  .contact__company { font-weight: 700; }
  .contact__lines { margin-top: 9px; font-size: 14.5px; line-height: 19.5px; }
  .contact__line { display: flex; align-items: center; gap: 8px; }
  .contact__line svg { width: 13px; height: 13px; fill: var(--brand-red); flex: none; }

  .url-band {
    position: absolute; left: 0; top: 295px;
    width: 534px; height: 29px;
    background: var(--brand-red);
    color: #fff; font-size: 14px; letter-spacing: 3px;
    display: flex; align-items: center; justify-content: center;
    padding-left: 80px;
  }
  .url-back {
    position: absolute; left: 0; width: 100%; top: 288px;
    text-align: center; color: #fff; font-size: 14px; letter-spacing: 4.5px;
  }
</style>
</head>
<body>
<main class="canvas">
  <section class="card card--front" aria-label="Vorderseite">
    <div class="wordmark">brightloom</div>
    <div class="divider"></div>
    <div class="contact">
      <p class="contact__name">MATTHIAS BRANDNER</p>
      <p class="contact__role">GESCHAFTSFUHRER</p>
      <p class="contact__address">
        <span class="contact__company">brightloom</span><br>
        Ahornweg 12<br>
        A4560 steinbach
      </p>
      <div class="contact__lines">
        <p class="contact__line">
          <svg viewBox="0 0 24 24" aria-hidden="true"><path d="M6.6 10.8a15.1 15.1 0 0 0 6.6 6.6l2.2-2.2a1 1 0 0 1 1-.25 11.4 11.4 0 0 0 3.6.57 1 1 0 0 1 1 1V20a1 1 0 0 1-1 1A17 17 0 0 1 3 4a1 1 0 0 1 1-1h3.5a1 1 0 0 1 1 1c0 1.25.2 2.45.57 3.57a1 1 0 0 1-.25 1z"/></svg>
          +43 660 417 392 5
        </p>
        <p class="contact__line">
          <svg viewBox="0 0 24 24" aria-hidden="true"><path d="M2 5h20v2l-10 6L2 7zM2 9.3l10 6 10-6V19H2z"/></svg>
          m.brandner@brightloom.eu
        </p>
      </div>
    </div>
    <div class="url-band">www.brightloom.eu</div>
  </section>

  <section class="card card--back" aria-label="Rückseite">
    <div class="wordmark">brightloom</div>
    <p class="url-back">www.brightloom.eu</p>
  </section>
</main>
</body>
</html>
```